Business card for law firm

Need business card for new law firm. Think confident, authoritative, conservative, but not stuffy or old-fashioned.

Contact Information for Business Card

Content for card - logo (uploaded), plus the following:

Paul Whitcombe (larger font)
Managing Partner (larger font, but not as large as name)
Level 9, 7 Ferris Lane
Sydney NSW 2000
Main Tel 02 9364 2710
Direct Tel 02 8472 3159
Email paul@qvlegal.com.au
www.qvlegal.com.au

Letterhead design should include logo plus:
Level 9, 7 Ferris Lane
Sydney NSW 2000
Tel 02 8472 3159
www.qvlegal.com.au

```html
<!DOCTYPE html>
<html lang="en">
<head>
<meta charset="utf-8">
<title>Quayvale Lawyers – Business Card</title>
<link rel="stylesheet" href="https://fonts.googleapis.com/css2?family=Cinzel:wght@400;500&family=Open+Sans:wght@400&display=swap">
<style>
  :root {
    --navy: #0b1f55;
    --white: #ffffff;
    --ink: #111111;
    --backdrop: #e4e4e6;
    --card-w: 520px;
    --card-h: 300px;
  }
  * { box-sizing: border-box; margin: 0; padding: 0; }
  html, body { width: 1200px; height: 900px; overflow: hidden; }
  body { background: var(--backdrop); position: relative; font-family: "Open Sans", Arial, sans-serif; }

  .card {
    position: absolute;
    width: var(--card-w);
    height: var(--card-h);
    border-radius: 22px;
    overflow: hidden;
    box-shadow: 0 4px 14px rgba(0,0,0,0.18);
  }
  .card--front { left: 90px; top: 130px; background: var(--navy); }
  .card--back { left: 590px; top: 470px; background: var(--white); }

  .wordmark { font-family: "Cinzel", "Times New Roman", serif; font-weight: 400; text-align: center; line-height: 1; }
  .wordmark__name { display: block; letter-spacing: 1px; }
  .wordmark__sub { display: block; letter-spacing: 0.9em; padding-left: 0.9em; }

  .card--front .wordmark { position: absolute; left: 0; right: 0; top: 118px; color: var(--white); }
  .card--front .wordmark__name { font-size: 44px; }
  .card--front .wordmark__sub { font-size: 13px; margin-top: 8px; }

  .card--back .wordmark { position: absolute; right: 30px; top: 34px; color: var(--ink); }
  .card--back .wordmark__name { font-size: 32px; }
  .card--back .wordmark__sub { font-size: 10px; margin-top: 6px; }

  .contact-band {
    position: absolute;
    left: 142px; right: 0; top: 118px; height: 130px;
    background: var(--navy);
    color: var(--white);
    padding: 10px 24px 0 0;
    text-align: right;
  }
  .corner-block {
    position: absolute;
    left: 24px; top: 118px; width: 108px; height: 130px;
    background: var(--navy);
  }
  .person__name { font-family: "Cinzel", "Times New Roman", serif; font-size: 17px; letter-spacing: 0.5px; line-height: 1.1; }
  .person__role { font-size: 12px; line-height: 1.3; margin-bottom: 4px; }
  .contact-list { list-style: none; font-size: 12px; line-height: 1.45; }
  .contact-list li { display: flex; justify-content: flex-end; align-items: center; gap: 5px; }
  .contact-list svg { width: 10px; height: 10px; fill: var(--white); flex: none; }
</style>
</head>
<body>
  <section class="card card--front" aria-label="Card front">
    <div class="wordmark">
      <span class="wordmark__name">QUAYVALE</span>
      <span class="wordmark__sub">LAWYERS</span>
    </div>
  </section>

  <section class="card card--back" aria-label="Card back">
    <div class="wordmark">
      <span class="wordmark__name">QUAYVALE</span>
      <span class="wordmark__sub">LAWYERS</span>
    </div>

    <div class="corner-block"></div>

    <div class="contact-band">
      <p class="person__name">PAUL WHITCOMBE</p>
      <p class="person__role">Managing Partner</p>
      <ul class="contact-list">
        <li>02 9364 2710
          <svg viewBox="0 0 10 10"><path d="M2 1h2l1 2.5-1.2 1A5 5 0 0 0 5.5 6.2l1-1.2L9 6v2a1 1 0 0 1-1 1A8 8 0 0 1 1 2a1 1 0 0 1 1-1z"/></svg></li>
        <li>02 8472 3159 (DIRECT)
          <svg viewBox="0 0 10 10"><path d="M2 1h2l1 2.5-1.2 1A5 5 0 0 0 5.5 6.2l1-1.2L9 6v2a1 1 0 0 1-1 1A8 8 0 0 1 1 2a1 1 0 0 1 1-1z"/></svg></li>
        <li>paul@qvlegal.com.au
          <svg viewBox="0 0 10 10"><path d="M0.5 2h9v6h-9z M1 2.5 5 5.5 9 2.5" stroke="#0b1f55" stroke-width="0.8"/></svg></li>
        <li>www.qvlegal.com.au
          <svg viewBox="0 0 10 10"><circle cx="5" cy="5" r="4.5"/><path d="M0.5 5h9M5 0.5c-2 2.5-2 6.5 0 9M5 0.5c2 2.5 2 6.5 0 9" stroke="#0b1f55" stroke-width="0.7" fill="none"/></svg></li>
      </ul>
    </div>
  </section>
</body>
</html>
```